Postcard design to acquire new clients for my Property Management Company

I'm looking for a postcard design that I can send to prospective clients detailing information about my company and services.
Postcard should be eye catching and contain information from www.bramblecrestpm.com. I've provided a few screen shots for the most important information and my logo.
Target Market(s)
Real Estate
Industry/Entity Type
Real Estate
Font styles to use
Sans Serif
Requirements
Must have
- Must be eye catching!! this will be a direct mail piece - I'd like for the card to be read and not tossed in the trash immediately.
Design que from the logo.
A place to write / print the receipts name and address.
our physical address - 2387 Hollow Pine Road, Lubbock, TX 79852.
Should not have
- the contact information on the business card is not accurate - please use info from website.

```html
<!DOCTYPE html>
<html lang="en">
<head>
<meta charset="UTF-8">
<title>Bramblecrest Property Management – Postcard</title>
<link href="https://fonts.googleapis.com/css2?family=Montserrat:wght@300;400;500;600;700;800&display=swap" rel="stylesheet">
<style>
  :root{
    --navy:#1f4784;
    --navy-dark:#17376b;
    --slate:#58595b;
    --grey-text:#6d6e71;
    --panel:#ececec;
    --line:#c9c9c9;
    --paper:#ffffff;
    --backdrop:#e4e2e3;
  }
  *{box-sizing:border-box;margin:0;padding:0}
  html,body{width:1200px;height:867px;overflow:hidden}
  body{background:var(--backdrop);font-family:'Montserrat',sans-serif;position:relative}
  .card{position:absolute;top:243px;width:560px;height:380px;background:var(--paper);overflow:hidden;box-shadow:0 10px 26px rgba(0,0,0,.18)}
  .card--back{left:30px}
  .card--front{left:610px}
  .abs{position:absolute}

  /* back */
  .offer-title{left:30px;top:40px;font-weight:800;font-size:25px;line-height:1.05;color:var(--slate);text-transform:uppercase}
  .offer-title .accent{color:var(--navy)}
  .offer-rule{left:30px;top:102px;width:270px;height:4px;background:var(--slate)}
  .offer-panel{left:30px;top:112px;width:270px;height:170px;background:var(--panel)}
  .offer-tag{left:30px;top:120px;width:180px;height:22px;background:var(--slate);color:#fff;font-size:11px;font-weight:600;padding:4px 14px;text-transform:uppercase}
  .offer-list{left:44px;top:156px;width:240px;list-style:none;color:var(--grey-text);font-size:11px;line-height:1.35}
  .offer-list li{margin-bottom:10px}
  .call-label{left:36px;top:292px;font-weight:700;font-size:15px;color:var(--slate);text-transform:uppercase}
  .call-pill{left:32px;top:312px;width:176px;height:32px;border-radius:16px;background:var(--navy);color:#fff;font-weight:800;font-size:20px;text-align:center;line-height:32px}
  .back-web{left:42px;top:350px;font-weight:700;font-size:12px;color:var(--slate)}
  .back-stripe{left:0;bottom:0;width:320px;height:8px;background:var(--navy)}
  .mail-divider{left:330px;top:150px;width:1px;height:190px;background:var(--line)}
  .mail-line{left:350px;width:180px;height:1px;background:var(--line)}

  /* front */
  .brand{left:28px;top:20px;display:flex;align-items:center;gap:6px}
  .brand-name{font-weight:700;font-size:17px;letter-spacing:1px;color:var(--navy)}
  .brand-mark{width:8px;height:8px;background:var(--navy)}
  .brand-sub{left:28px;top:42px;font-size:8px;font-weight:500;letter-spacing:1.2px;color:var(--navy)}
  .photo{left:230px;top:55px;width:330px;height:170px;background:linear-gradient(120deg,#dfe6ee 0%,#b9c6d6 45%,#4a5f7d 70%,#8ea3bb 100%)}
  .headline{left:28px;top:80px;color:var(--slate);text-transform:uppercase}
  .headline .kicker{font-size:14px;font-weight:400;letter-spacing:.5px}
  .headline .main{font-size:28px;font-weight:800;line-height:1;color:var(--navy)}
  .headline .tail{font-size:14px;font-weight:400}
  .shapes{left:0;top:0}
  .services-title{right:18px;top:200px;color:#fff;font-weight:800;font-size:18px}
  .services-sub{right:18px;top:223px;color:#fff;font-size:8.5px;font-weight:500}
  .service-row{left:10px;top:250px;width:545px;display:flex;justify-content:space-between}
  .service{width:64px;text-align:center;font-size:7.5px;line-height:1.2;color:var(--slate);font-weight:500}
  .service-icon{width:30px;height:30px;margin:0 auto 4px;border:1.5px solid var(--navy);border-radius:50%;display:flex;align-items:center;justify-content:center}
  .service-icon svg{width:16px;height:16px}
  .address{left:28px;top:316px;color:#fff;font-size:10px;line-height:1.25;display:flex;gap:8px;align-items:center}
  .phone{left:220px;top:338px;font-weight:700;font-size:15px;color:var(--slate);display:flex;gap:6px;align-items:center}
  .front-web{right:20px;top:356px;font-weight:700;font-size:11px;color:var(--slate);display:flex;gap:5px;align-items:center}
</style>
</head>
<body>

<section class="card card--back" aria-label="Postcard back">
  <h2 class="abs offer-title">Get a <span class="accent">free</span><br>Rental analysis</h2>
  <div class="abs offer-rule"></div>
  <div class="abs offer-panel"></div>
  <div class="abs offer-tag">Get a free</div>
  <ul class="abs offer-list">
    <li>Determine the rental value of your property.</li>
    <li>Find out how to get the most out of your investment.</li>
    <li>See if your home fits our management approach.</li>
  </ul>
  <div class="abs call-label">Give us a call now</div>
  <div class="abs call-pill">806-555-0142</div>
  <div class="abs back-web">www.bramblecrestpm.com</div>
  <div class="abs back-stripe"></div>
  <div class="abs mail-divider"></div>
  <div class="abs mail-line" style="top:250px"></div>
  <div class="abs mail-line" style="top:275px"></div>
  <div class="abs mail-line" style="top:300px"></div>
</section>

<section class="card card--front" aria-label="Postcard front">
  <div class="abs photo" role="img" aria-label="Photo of two property managers reviewing a laptop in a bright apartment"></div>
  <svg class="abs shapes" width="560" height="380" viewBox="0 0 560 380">
    <rect class="band-top" x="0" y="178" width="300" height="14" fill="#1f4784"/>
    <path class="services-band" d="M240 192 L560 192 L560 242 L300 242 C280 242 272 222 240 222 Z" fill="#1f4784"/>
    <path class="address-band" d="M0 300 L180 300 C200 300 205 345 230 345 L0 345 Z" fill="#58595b"/>
    <rect class="footer-band" x="300" y="372" width="260" height="8" fill="#58595b"/>
  </svg>
  <div class="abs brand"><span class="brand-name">BRAMBLECREST</span><span class="brand-mark"></span></div>
  <div class="abs brand-sub">PROPERTY MANAGEMENT</div>
  <h1 class="abs headline">
    <div class="kicker">Choose the right</div>
    <div class="main">Property<br>Management</div>
    <div class="tail">System</div>
  </h1>
  <div class="abs services-title">OUR SERVICES</div>
  <div class="abs services-sub">We offer full-service property management solutions</div>

  <div class="abs service-row">
    <div class="service"><div class="service-icon"><svg viewBox="0 0 16 16"><path d="M2 8 L8 2 L14 8 L12 8 L12 14 L4 14 L4 8 Z" fill="#58595b"/></svg></div>Property<br>Marketing</div>
    <div class="service"><div class="service-icon"><svg viewBox="0 0 16 16" fill="#58595b"><circle cx="8" cy="5" r="2.5"/><circle cx="3.5" cy="6" r="2"/><circle cx="12.5" cy="6" r="2"/><path d="M3 14 C3 9 13 9 13 14 Z"/></svg></div>Tenant<br>Screening</div>
    <div class="service"><div class="service-icon"><svg viewBox="0 0 16 16"><text x="8" y="13" font-size="13" font-weight="700" text-anchor="middle" fill="#58595b" font-family="Montserrat,sans-serif">$</text></svg></div>Rent<br>Collection</div>
    <div class="service"><div class="service-icon"><svg viewBox="0 0 16 16" fill="#58595b"><rect x="3" y="2" width="10" height="4" rx="1"/><rect x="7" y="5" width="2.5" height="10"/></svg></div>Maintenance</div>
    <div class="service"><div class="service-icon"><svg viewBox="0 0 16 16"><circle cx="6.5" cy="6.5" r="4" fill="none" stroke="#58595b" stroke-width="2"/><path d="M9.5 9.5 L14 14" stroke="#58595b" stroke-width="2.5"/></svg></div>Property<br>Inspections</div>
    <div class="service"><div class="service-icon"><svg viewBox="0 0 16 16" fill="#58595b"><rect x="2" y="2" width="12" height="12" fill="none" stroke="#58595b" stroke-width="1.5"/><rect x="4" y="9" width="2" height="3"/><rect x="7" y="6" width="2" height="6"/><rect x="10" y="4" width="2" height="8"/></svg></div>Financial<br>Reporting</div>
    <div class="service"><div class="service-icon"><svg viewBox="0 0 16 16"><path d="M8 1 L14 3 L14 8 C14 11 11 14 8 15 C5 14 2 11 2 8 L2 3 Z" fill="#58595b"/></svg></div>Evictions</div>
    <div class="service"><div class="service-icon"><svg viewBox="0 0 16 16" stroke="#58595b" stroke-width="1.4" fill="none"><path d="M8 2 L8 14 M4 14 L12 14 M2 4 L14 4"/><path d="M1 9 L3 4 L5 9 Z M11 9 L13 4 L15 9 Z" fill="#58595b"/></svg></div>Legal<br>Guidance</div>
  </div>

  <div class="abs address">
    <svg width="10" height="14" viewBox="0 0 10 14"><path d="M5 0 C2 0 0 2.2 0 5 C0 8.5 5 14 5 14 C5 14 10 8.5 10 5 C10 2.2 8 0 5 0 Z" fill="#fff"/><circle cx="5" cy="5" r="1.8" fill="#58595b"/></svg>
    <span>2387 Hollow Pine Road<br>Lubbock, TX 79852</span>
  </div>
  <div class="abs phone">
    <svg width="13" height="13" viewBox="0 0 16 16"><path d="M3 1 L6 1 L7 5 L5 6.5 C6 9 7 10 9.5 11 L11 9 L15 10 L15 13 C15 14 14 15 13 15 C6 15 1 10 1 3 C1 2 2 1 3 1 Z" fill="#1f4784"/></svg>
    <span>806-555-0142</span>
  </div>
  <div class="abs front-web">
    <svg width="10" height="10" viewBox="0 0 10 10"><circle cx="5" cy="5" r="4.5" fill="#1f4784"/></svg>
    <span>www.bramblecrestpm.com</span>
  </div>
</section>

</body>
</html>
```